Bry7Legal Letterhead

Need a new letterhead for my law firm.
IDENTIFYING INFORMATION BELOW:
Anselmo R Quintara III
Attorney at Law
Address: 2847 Larkspur Blvd, Ste 300, Dallas, TX 75204
Phone: 877-482-6017
Fax: 469-738-1452
Email: bry@bry7legal.example
Website: www.bry7legal.example

Colors
0054AA
0677BA
7BADD7
CADEEF
E8F1F8

Requirements
Must have
• Logo needs to be on the letterhead, along with identifying information which is included in the project description.

```html
<!DOCTYPE html>
<html lang="en">
<head>
<meta charset="utf-8">
<title>Quintara &amp; Associates Letterhead</title>
<link href="https://fonts.googleapis.com/css2?family=Montserrat:wght@400;500;700;800&display=swap" rel="stylesheet">
<style>
  :root {
    --ink: #1b1b1b;
    --text: #2a2a2a;
    --navy: #0054AA;
    --blue: #0677BA;
    --sky: #0a8fd8;
    --page-bg: #f4f5f7;
    --paper: #ffffff;
  }
  html, body {
    margin: 0;
    width: 1200px;
    height: 2804px;
    overflow: hidden;
    background: var(--page-bg);
    font-family: "Montserrat", sans-serif;
    color: var(--text);
  }
  .sheet {
    position: absolute;
    left: 80px;
    top: 665px;
    width: 1040px;
    height: 1474px;
    background: var(--paper);
    box-shadow: 0 8px 34px rgba(0,0,0,0.22);
    overflow: hidden;
  }
  .brand { position: absolute; left: 71px; top: 62px; }
  .brand-name {
    font-weight: 700;
    font-size: 46px;
    letter-spacing: 0.5px;
    color: var(--ink);
    line-height: 1;
  }
  .brand-tagline {
    margin: 12px 0 0 66px;
    font-weight: 400;
    font-size: 25px;
    letter-spacing: 5px;
    color: var(--ink);
  }
  .salutation {
    position: absolute; left: 77px; top: 222px;
    font-size: 23px; font-weight: 500; color: var(--ink);
  }
  .letter-body {
    position: absolute; left: 71px; top: 279px; width: 886px;
  }
  .letter-body p {
    margin: 0 0 21px;
    font-size: 16px;
    line-height: 21px;
    text-align: justify;
  }
  .signature { position: absolute; left: 71px; top: 1100px; }
  .signature-line {
    width: 385px; height: 2px; margin-left: 10px;
    background: repeating-linear-gradient(90deg, var(--ink) 0 12px, transparent 12px 16px);
  }
  .signer-name { margin-top: 24px; font-size: 25px; font-weight: 800; color: var(--ink); letter-spacing: -0.3px; line-height: 1.2; }
  .signer-title { margin-top: 8px; font-size: 24px; font-weight: 400; color: var(--ink); line-height: 1.2; }
  .contact-list {
    position: absolute; left: 80px; top: 1268px;
    margin: 0; padding: 0; list-style: none;
  }
  .contact-list li {
    display: flex; align-items: center;
    height: 28px; font-size: 20px; color: var(--ink);
  }
  .contact-list li.strong { font-weight: 700; }
  .contact-list svg { width: 22px; height: 22px; margin-right: 30px; flex: none; }
  .footer-band { position: absolute; left: 0; bottom: 0; width: 1040px; height: 30px; }
</style>
</head>
<body>
  <div class="sheet">
    <header class="brand">
      <div class="brand-name">Quintara &amp; Associates</div>
      <div class="brand-tagline">LEGAL MADE CLEAR</div>
    </header>

    <div class="salutation">Dear Sir,</div>

    <section class="letter-body">
      <p>Quis ipsum suspendisse ultrices gravida. Risus commodo viverra maecenas accumsan lacus vel facilisis. Lorem ipsum dolor sit amet, consectetur adipiscing elit, sed do eiusmod tempor incididunt ut labore et dolore magna aliqua. Quis ipsum suspendisse ultrices gravida. Risus commodo viverra maecenas accumsan lacus vel facilisis. Lorem ipsum dolor sit amet, consectetur adipiscing elit, sed do eiusmod tempor incididunt ut labore et dolore magna aliqua. Quis ipsum suspendisse ultrices gravida. Risus commodo viverra maecenas accumsan lacus vel facilisis. Lorem ipsum dolor sit amet, consectetur adipiscing elit, sed do eiusmod tempor incididunt ut labore et dolore magna aliqua. Quis ipsum suspendisse ultrices gravida. Risus commodo viverra maecenas accumsan lacus vel facilisis.</p>
      <p>Lorem ipsum dolor sit amet, consectetur adipiscing elit, sed do eiusmod tempor incididunt ut labore et dolore magna aliqua. Quis ipsum suspendisse ultrices gravida. Risus commodo viverra maecenas accumsan lacus vel facilisis. Lorem ipsum dolor sit amet, consectetur adipiscing elit, sed do eiusmod tempor incididunt ut labore et dolore magna aliqua. Quis ipsum suspendisse ultrices gravida. Risus commodo viverra maecenas accumsan lacus vel facilisis. Lorem ipsum dolor sit amet, consectetur adipiscing elit, sed do eiusmod tempor incididunt ut labore et dolore magna aliqua. Quis ipsum suspendisse ultrices gravida. Risus commodo viverra maecenas accumsan lacus vel facilisis. Lorem ipsum dolor sit amet, consectetur adipiscing elit, sed do eiusmod tempor incididunt ut labore et dolore magna aliqua. Quis ipsum suspendisse ultrices gravida. Risus commodo viverra maecenas accumsan lacus vel facilisis.</p>
      <p>Lorem ipsum dolor sit amet, consectetur adipiscing elit, sed do eiusmod tempor incididunt ut labore et dolore magna aliqua. Quis ipsum suspendisse ultrices gravida. Risus commodo viverra maecenas accumsan lacus vel facilisis. Lorem ipsum dolor sit amet, consectetur adipiscing elit, sed do eiusmod tempor incididunt ut labore et dolore magna aliqua. Quis ipsum suspendisse ultrices gravida. Risus commodo viverra maecenas accumsan lacus vel facilisis. Lorem ipsum dolor sit amet, consectetur adipiscing elit, sed do eiusmod tempor incididunt ut labore et dolore magna aliqua. Quis ipsum suspendisse ultrices gravida. Risus commodo viverra maecenas accumsan lacus vel facilisis. Lorem ipsum dolor sit amet, consectetur adipiscing elit, sed do eiusmod tempor incididunt ut labore et dolore magna aliqua. Quis ipsum suspendisse ultrices gravida. Risus commodo viverra maecenas accumsan lacus vel facilisis. Lorem ipsum dolor sit amet, consectetur adipiscing elit, sed do eiusmod tempor incididunt ut labore et dolore magna aliqua. Quis ipsum suspendisse ultrices gravida. Risus commodo viverra maecenas accumsan lacus vel facilisis. Lorem ipsum dolor sit amet, consectetur adipiscing elit, sed do eiusmod tempor incididunt ut labore et dolore magna aliqua. Quis ipsum suspendisse ultrices gravida. Risus commodo viverra maecenas accumsan lacus vel facilisis.</p>
    </section>

    <section class="signature">
      <div class="signature-line"></div>
      <div class="signer-name">Anselmo R Quintara III</div>
      <div class="signer-title">Attorney at Law</div>
    </section>

    <ul class="contact-list">
      <li class="strong">
        <svg viewBox="0 0 24 24" aria-hidden="true"><path fill="var(--navy)" d="M6.6 10.8a15.1 15.1 0 0 0 6.6 6.6l2.2-2.2c.3-.3.7-.4 1-.2 1.1.4 2.3.6 3.6.6.6 0 1 .4 1 1V20c0 .6-.4 1-1 1A17 17 0 0 1 3 4c0-.6.4-1 1-1h3.5c.6 0 1 .4 1 1 0 1.3.2 2.5.6 3.6.1.3 0 .7-.2 1z"/></svg>
        877-482-6017
      </li>
      <li class="strong">
        <svg viewBox="0 0 24 24" aria-hidden="true"><path fill="var(--navy)" d="M7 3h8l2 2v4H7zM4 10h16a1 1 0 0 1 1 1v7h-4v3H7v-3H3v-7a1 1 0 0 1 1-1zm5 6v3h6v-3z"/></svg>
        469-738-1452
      </li>
      <li>
        <svg viewBox="0 0 24 24" aria-hidden="true"><path fill="var(--navy)" d="M3 5h18v14H3zm2 2v.5l7 5 7-5V7zm0 3v7h14v-7l-7 5z"/></svg>
        bry@bry7legal.example
      </li>
      <li>
        <svg viewBox="0 0 24 24" aria-hidden="true"><circle cx="12" cy="12" r="9" fill="none" stroke="var(--navy)" stroke-width="2"/><path d="M3 12h18M12 3c3 3 3 15 0 18M12 3c-3 3-3 15 0 18" fill="none" stroke="var(--navy)" stroke-width="1.6"/></svg>
        www.bry7legal.example
      </li>
      <li>
        <svg viewBox="0 0 24 24" aria-hidden="true"><path fill="var(--navy)" d="M12 2a6 6 0 0 1 6 6c0 4.5-6 10-6 10S6 12.5 6 8a6 6 0 0 1 6-6zm0 3.5a2.5 2.5 0 1 0 0 5 2.5 2.5 0 0 0 0-5z"/><ellipse cx="12" cy="20.5" rx="7" ry="1.8" fill="none" stroke="var(--navy)" stroke-width="1.5"/></svg>
        2847 Larkspur Blvd, Ste 300, Dallas, TX 75204
      </li>
    </ul>

    <svg class="footer-band" viewBox="0 0 1040 30" preserveAspectRatio="none" aria-hidden="true">
      <rect x="0" y="16" width="1040" height="14" fill="var(--navy)"/>
      <path d="M706 30 C724 8 742 2 770 2 H1040 V30 Z" fill="#ffffff"/>
      <path d="M714 30 C732 10 748 4 774 4 H1040 V30 Z" fill="var(--sky)"/>
    </svg>
  </div>
</body>
</html>
```